Harbor Crestline (Business Card Design)

Need business cards designed. Something modern, chic, and sleek. Mabye the back of the card should be the navy blue that is in the logo and then just the logo on the back.

Target Market(s)

Those in the hotel, office, and renovation industry

Contact Information for Business Card

1. Logo 2. Dorian Fenwick 3. CEO/Founder 4. Phone: (833) HarbCre / (833) 427-2731 5. Email: dorian@theharborcrestline.com 6. Website: www.theharborcrestline.com

Font styles to use
Other font styles liked:
• Look at the logo font and base the font for everything else off of that.

Colors
0054AA
0677BA
7BADD7
CADEEF
E8F1F8

Requirements
Must have
• Colors that are associated in the logo
Nice to have
• Sleek modern clean and chic design.

```html
<!DOCTYPE html>
<html lang="en">
<head>
<meta charset="utf-8">
<title>Harbor Crestline — Business Card</title>
<link href="https://fonts.googleapis.com/css2?family=Open+Sans:wght@400;600;700&display=swap" rel="stylesheet">
<style>
  :root {
    --navy: #0c1740;
    --gold: #c9a043;
    --white: #ffffff;
    --backdrop: #2a2b2e;
    --divider: rgba(255,255,255,0.45);
  }
  html, body {
    margin: 0;
    width: 1200px;
    height: 780px;
    overflow: hidden;
    background: var(--backdrop);
    font-family: "Open Sans", Arial, sans-serif;
  }
  .canvas {
    width: 1200px;
    height: 780px;
    display: flex;
    align-items: center;
    justify-content: center;
    gap: 40px;
  }
  .card {
    position: relative;
    width: 540px;
    height: 309px;
    background: var(--navy);
    border-radius: 3px;
    overflow: hidden;
    box-shadow: 0 10px 30px rgba(0,0,0,0.45);
  }
  .wordmark {
    display: flex;
    align-items: center;
    gap: 10px;
    color: var(--white);
    font-weight: 600;
    text-transform: uppercase;
    letter-spacing: 0.14em;
    white-space: nowrap;
  }
  .wordmark__square {
    width: 12px;
    height: 12px;
    background: var(--gold);
    flex: none;
  }
  /* front */
  .card--front .wordmark {
    position: absolute;
    top: 58px;
    left: 50%;
    transform: translateX(-50%);
    font-size: 19px;
  }
  .identity {
    position: absolute;
    top: 118px;
    right: 300px;
    text-align: right;
  }
  .identity__name {
    margin: 0;
    font-size: 27px;
    line-height: 1.1;
    font-weight: 700;
    color: var(--gold);
    white-space: nowrap;
  }
  .identity__name span { color: var(--white); }
  .identity__title {
    margin: 4px 0 0;
    font-size: 13px;
    color: var(--white);
  }
  .divider {
    position: absolute;
    top: 118px;
    left: 258px;
    width: 1px;
    height: 88px;
    background: var(--divider);
  }
  .contacts {
    position: absolute;
    top: 124px;
    left: 274px;
    margin: 0;
    padding: 0;
    list-style: none;
  }
  .contacts li {
    display: flex;
    align-items: center;
    gap: 7px;
    font-size: 12px;
    line-height: 25px;
    color: var(--white);
    white-space: nowrap;
  }
  .contacts svg { width: 13px; height: 13px; flex: none; }
  .address-band {
    position: absolute;
    left: 0;
    right: 0;
    bottom: 0;
    height: 38px;
    background: var(--gold);
    display: flex;
    align-items: center;
    padding-left: 26px;
    font-size: 14px;
    color: var(--white);
  }
  /* back */
  .card--back {
    display: flex;
    align-items: center;
    justify-content: center;
  }
  .card--back .wordmark { font-size: 24px; }
</style>
</head>
<body>
<main class="canvas">
  <section class="card card--front" aria-label="Business card front">
    <div class="wordmark"><span class="wordmark__square"></span>Harbor Crestline</div>

    <div class="identity">
      <p class="identity__name">Dorian <span>Fenwick</span></p>
      <p class="identity__title">CEO/Founder</p>
    </div>

    <div class="divider"></div>

    <ul class="contacts">
      <li>
        <svg viewBox="0 0 16 16" aria-hidden="true"><circle cx="8" cy="8" r="8" fill="var(--gold)"/><path d="M5.2 4.2l1.5 1.6-.7 1.1c.5 1 1.2 1.7 2.2 2.2l1.1-.7 1.6 1.5-.8 1.4C7.4 11.3 4.7 8.6 4 5z" fill="var(--navy)"/></svg>
        (833) HarbCre / (833) 427-2731
      </li>
      <li>
        <svg viewBox="0 0 16 16" aria-hidden="true"><circle cx="8" cy="8" r="8" fill="var(--gold)"/><circle cx="8" cy="8" r="4.5" fill="none" stroke="var(--navy)" stroke-width="1"/><path d="M3.5 8h9M8 3.5c-2 2.5-2 6.5 0 9M8 3.5c2 2.5 2 6.5 0 9" fill="none" stroke="var(--navy)" stroke-width="0.9"/></svg>
        www.theharborcrestline.com
      </li>
      <li>
        <svg viewBox="0 0 16 16" aria-hidden="true"><circle cx="8" cy="8" r="8" fill="var(--gold)"/><rect x="4" y="5.2" width="8" height="5.6" fill="none" stroke="var(--navy)" stroke-width="1"/><path d="M4 5.4l4 3 4-3" fill="none" stroke="var(--navy)" stroke-width="1"/></svg>
        dorian@theharborcrestline.com
      </li>
    </ul>

    <div class="address-band">4120 Linden Ridge Rd Suite 210, Easton, MD 21601</div>
  </section>

  <section class="card card--back" aria-label="Business card back">
    <div class="wordmark"><span class="wordmark__square"></span>Harbor Crestline</div>
  </section>
</main>
</body>
</html>
```